Marlo clean Business Cards

I'm looking for someone to design my business card using my company name and logo. I would like it it be clean, fresh and a little out of the box. The colors I would like used are the same two in my logo (gold and the teal blue color) I also want it to screen high end scene the company name is Marlo clean :) I'm a commercial cleaning company based out of Orange and San Diego county. Once I receive your email I will send over the file. Because the file is quote big with several options of logos. Please be an out of the box thinker and take some risk...I'm looking for someone to put themselves out there. Thanks and good luck

```html
<!DOCTYPE html>
<html lang="en">
<head>
<meta charset="utf-8">
<title>Marlo clean – Business Card</title>
<link rel="stylesheet" href="https://fonts.googleapis.com/css2?family=Open+Sans:wght@400;600;700&display=swap">
<style>
  :root{
    --backdrop:#2b2b2d;
    --card-white:#f8f8f7;
    --card-grey:#e4e4e3;
    --charcoal:#343638;
    --ink:#2f2f31;
    --teal:#178a96;
    --gold:#c9a448;
    --light:#ffffff;
  }
  *{margin:0;padding:0;box-sizing:border-box}
  html,body{width:1200px;height:816px;overflow:hidden;background:var(--backdrop)}
  body{font-family:"Open Sans",Arial,sans-serif;position:relative}
  .card{
    position:absolute;left:75px;top:108px;width:1050px;height:600px;
    border-radius:40px;overflow:hidden;
    background:radial-gradient(ellipse at 60% 30%,var(--card-white) 0%,var(--card-white) 40%,var(--card-grey) 100%);
  }
  .card-shapes{position:absolute;inset:0}
  .band-dark{fill:var(--charcoal)}
  .band-teal{fill:var(--teal)}
  .gold-edge{fill:none;stroke:var(--gold);stroke-width:5}
  .gold-rule{fill:var(--gold)}
  .person{position:absolute;left:58px;top:178px}
  .person-name{font-weight:700;font-size:38px;color:var(--ink);letter-spacing:0.5px;line-height:1.1}
  .person-title{font-weight:400;font-size:29px;color:var(--teal);line-height:1.25}
  .contact{position:absolute;left:58px;top:318px;list-style:none;color:var(--ink)}
  .contact li{display:flex;align-items:flex-start;font-size:24px;line-height:31px}
  .contact .address{font-weight:600;margin-bottom:4px}
  .contact svg{width:22px;height:22px;margin:5px 14px 0 0;flex:none;fill:var(--gold)}
  .contact .address svg{margin-top:4px}
  .brand{position:absolute;left:540px;top:210px;display:flex;align-items:center;gap:20px}
  .brand-dot{width:50px;height:50px;border-radius:50%;background:var(--gold);flex:none}
  .brand-name{font-weight:600;font-size:60px;color:var(--ink);letter-spacing:3px;line-height:1}
  .website{position:absolute;left:548px;top:365px;height:75px;width:480px;display:flex;align-items:center;justify-content:center;
    color:var(--light);font-size:33px;font-weight:400;letter-spacing:0.3px}
</style>
</head>
<body>
  <section class="card">
    <svg class="card-shapes" viewBox="0 0 1050 600" width="1050" height="600" aria-hidden="true">
      <path class="band-dark" d="M0,505 H450 C500,505 490,440 545,440 H1050 V600 H0 Z"/>
      <path class="gold-edge" d="M0,505 H450 C500,505 490,440 545,440 H1050"/>
      <path class="band-teal" d="M1050,365 H548 A37.5,37.5 0 0 0 548,440 H1050 Z"/>
      <rect class="gold-rule" x="58" y="290" width="70" height="4" rx="2"/>
    </svg>

    <div class="person">
      <p class="person-name">DANA WHITFIELD</p>
      <p class="person-title">Managing Director</p>
    </div>

    <ul class="contact">
      <li class="address">
        <svg viewBox="0 0 24 24"><path d="M12 1a8 8 0 0 0-8 8c0 6 8 14 8 14s8-8 8-14a8 8 0 0 0-8-8zm0 11a3 3 0 1 1 0-6 3 3 0 0 1 0 6z"/></svg>
        <span>214 Harbor View Suite 9,<br>Irvine CA</span>
      </li>
      <li>
        <svg viewBox="0 0 24 24"><path d="M2 9c2-4 18-4 20 0v3h-5l-1-3H8l-1 3H2zM5 13h14l2 8H3z"/></svg>
        <span>949 555 0142</span>
      </li>
      <li>
        <svg viewBox="0 0 24 24"><path d="M6 2h9l3 3v5h-2V6h-3V4H8v6H6zM3 11h18v11H3zm4 3v2h4v-2zm0 4v2h4v-2zm7-4v6h4v-6z"/></svg>
        <span>949 555 0178</span>
      </li>
      <li>
        <svg viewBox="0 0 24 24"><path d="M2 5h20v14H2zm2 2v1l8 5 8-5V7l-8 5z"/></svg>
        <span>dana@marlomail.com</span>
      </li>
    </ul>

    <div class="brand">
      <span class="brand-dot"></span>
      <span class="brand-name">Marlo clean</span>
    </div>

    <p class="website">www.marlocleanco.com</p>
  </section>
</body>
</html>
```